BLS Business Card 2018

Larkmere Chiropractic. We have two locations that we want to advertise on the same card. Brightvale OrthoCore campus address: 3815 Pellham Dr., Suite 240, Flowood, MS 39417. Madison address: 246 Willowmere Dr., Building D., Madison, MS 39284. website: www.drlarkmere-example.com. o:(601)555-0147 f:(601)555-0183

Target Market(s)

Health care decision makers: primary care doctors and mothers

Contact Information for Business Card

I have no idea; up for any suggestions and I'd do much better picking from examples versus describing what I'm looking for. We are in a very high end location and would like the cards to look really sharp.

Requirements
Must have
• My name, Martin R Belvane, D.C.

```html
<!DOCTYPE html>
<html lang="en">
<head>
<meta charset="utf-8">
<title>Larkmere Chiropractic – Business Card</title>
<link rel="stylesheet" href="https://fonts.googleapis.com/css2?family=Roboto:wght@400;500&family=Roboto+Condensed:wght@700&display=swap">
<style>
  :root {
    --page-bg: #ecebe8;
    --card-dark: #1b1c1e;
    --card-light: #f4f4f3;
    --ink-light: #ffffff;
    --ink-dark: #111111;
    --divider: rgba(255,255,255,0.75);
  }
  * { margin: 0; padding: 0; box-sizing: border-box; }
  html, body {
    width: 1200px; height: 960px; overflow: hidden;
    background: var(--page-bg);
    font-family: "Roboto", Arial, sans-serif;
  }
  .canvas { position: relative; width: 1200px; height: 960px; }
  .card {
    position: absolute; width: 600px; height: 342px;
    box-shadow: 0 2px 6px rgba(0,0,0,0.25);
  }
  .card--front { left: 315px; top: 113px; background: var(--card-dark); color: var(--ink-light); }
  .card--back { left: 311px; top: 472px; background: var(--card-light); color: var(--ink-dark); }

  .brand-name {
    position: absolute; font-weight: 400; white-space: nowrap;
    letter-spacing: 0.5px;
  }
  .card--front .brand-name { left: 72px; top: 152px; font-size: 21px; color: var(--ink-light); }
  .card--back .brand-name { left: 0; width: 600px; text-align: center; top: 142px; font-size: 30px; color: var(--ink-dark); }

  .divider {
    position: absolute; left: 318px; top: 122px; width: 1px; height: 90px;
    background: var(--divider);
  }
  .contact-list {
    position: absolute; left: 340px; top: 136px; list-style: none;
    font-size: 14px; line-height: 19.5px;
  }
  .contact-list li { display: flex; align-items: center; gap: 8px; }
  .contact-list svg { width: 13px; height: 13px; fill: var(--ink-light); flex: none; }

  .locations {
    position: absolute; left: 0; width: 600px; top: 252px;
    text-align: center; font-size: 14px; line-height: 23px;
  }
  .practitioner {
    position: absolute; left: 0; width: 600px; top: 255px; text-align: center;
    font-family: "Roboto Condensed", Arial, sans-serif; font-weight: 700; font-size: 21px;
  }
</style>
</head>
<body>
<main class="canvas">
  <section class="card card--front" aria-label="Card front">
    <div class="brand-name">Larkmere Chiropractic</div>
    <div class="divider"></div>
    <ul class="contact-list">
      <li><svg viewBox="0 0 24 24" aria-hidden="true"><path d="M6.6 10.8a15.2 15.2 0 0 0 6.6 6.6l2.2-2.2c.3-.3.7-.4 1-.2 1.1.4 2.3.6 3.6.6.6 0 1 .4 1 1V20c0 .6-.4 1-1 1A17 17 0 0 1 3 4c0-.6.4-1 1-1h3.5c.6 0 1 .4 1 1 0 1.3.2 2.5.6 3.6.1.3 0 .7-.2 1z"/></svg>(601)555-0147</li>
      <li><svg viewBox="0 0 24 24" aria-hidden="true"><path d="M6 2h10l2 2v5H6z M3 10h18v9h-3v3H6v-3H3z M8 16v4h8v-4z"/></svg>(601)555-0183</li>
      <li><svg viewBox="0 0 24 24" aria-hidden="true"><path d="M12 2a10 10 0 1 0 0 20 10 10 0 0 0 0-20zm-1 17.9A8 8 0 0 1 4.2 10L9 15v1c0 1.1.9 2 2 2zm6.9-2.5A2 2 0 0 0 16 16h-1v-3c0-.6-.4-1-1-1H8v-2h2c.6 0 1-.4 1-1V7h2a2 2 0 0 0 2-2v-.4a8 8 0 0 1 2.9 12.8z"/></svg>www.drlarkmere-example.com</li>
    </ul>
    <p class="locations">
      Brightvale OrthoCore campus : 3815 Pellham Dr., Suite 240, Flowood, MS 39417.<br>
      Madison address: 246 Willowmere Dr., Building D., Madison, MS 39284.
    </p>
  </section>

  <section class="card card--back" aria-label="Card back">
    <div class="brand-name">Larkmere Chiropractic</div>
    <p class="practitioner">MARTIN R BELVANE, D.C.</p>
  </section>
</main>
</body>
</html>
```